Podcast Cover Art Design for Divorce Support

Need a podcast cover art design for new podcast that will cover Emotional Divorce Support and Recovery topics. People are lost, confused. They are looking for help during the confusion and heartbreak. Main Title is "Quiet Harbor Podcast". Subtitle is "Finding Your Steady Ground". We want a design that is encouraging yet not overly "happy". We also want to convey kindness, clarity, and strength, if possible. Our logo colors use grey and red though we aren't tied to those colors for the podcast. Logo may be used on the podcast but not required. Final image should be 3000x3000px. Our logo uses Montserrat-Medium and Multi-SemiBold. Not necessary but available if you want to use it.

```html
<!DOCTYPE html>
<html lang="en">
<head>
<meta charset="UTF-8">
<title>Quiet Harbor Podcast — Cover Art</title>
<link rel="stylesheet" href="https://fonts.googleapis.com/css2?family=Montserrat:wght@500;600;800&display=swap">
<style>
  :root {
    --brand-red: #ec1c24;
    --brand-grey: #7f7f7f;
    --band-text: #ffffff;
    --paper-light: #fafafa;
    --paper-edge: #e4e4e4;
    --photo-deep: #8e0a0c;
    --photo-red: #d40d12;
    --photo-warm: #b07a5e;
  }
  html, body {
    margin: 0;
    padding: 0;
    width: 1200px;
    height: 1200px;
    overflow: hidden;
  }
  .cover {
    position: relative;
    width: 1200px;
    height: 1200px;
    background: radial-gradient(circle at 50% 45%, var(--paper-light) 0%, #f0f0f0 50%, var(--paper-edge) 100%);
    font-family: "Montserrat", Arial, sans-serif;
  }
  .title-main {
    position: absolute;
    left: 82px;
    top: 34px;
    margin: 0;
    font-weight: 800;
    font-size: 222px;
    line-height: 1;
    letter-spacing: -4px;
    color: var(--brand-red);
  }
  .title-row {
    position: absolute;
    left: 84px;
    width: 1033px;
    top: 228px;
    display: flex;
    align-items: baseline;
    justify-content: space-between;
  }
  .title-second {
    margin: 0;
    font-weight: 800;
    font-size: 132px;
    line-height: 1;
    letter-spacing: -2px;
    color: var(--brand-grey);
  }
  .title-tag {
    font-weight: 500;
    font-size: 50px;
    letter-spacing: 17px;
    margin-right: -17px;
    color: var(--brand-red);
  }
  .subtitle-band {
    position: absolute;
    left: 84px;
    top: 376px;
    width: 1033px;
    height: 96px;
    background: var(--brand-grey);
    display: flex;
    align-items: center;
    justify-content: center;
  }
  .subtitle-band p {
    margin: 0;
    font-weight: 500;
    font-size: 52px;
    color: var(--band-text);
    letter-spacing: 0.5px;
  }
  .heart-photo {
    position: absolute;
    left: 262px;
    top: 510px;
    width: 691px;
    height: 634px;
  }
</style>
</head>
<body>
  <main class="cover">
    <h1 class="title-main">QUIET</h1>
    <div class="title-row">
      <h2 class="title-second">HARBOR</h2>
      <span class="title-tag">PODCAST</span>
    </div>
    <div class="subtitle-band"><p>FINDING YOUR STEADY GROUND</p></div>
    <svg class="heart-photo" viewBox="0 0 691 634" role="img" aria-label="Heart-shaped photo of two people holding hands in comfort, set against red clothing">
      <defs>
        <radialGradient id="heartFill" cx="0.5" cy="0.55" r="0.6">
          <stop offset="0" stop-color="var(--photo-warm)"/>
          <stop offset="0.45" stop-color="#a0402e"/>
          <stop offset="0.75" stop-color="var(--photo-red)"/>
          <stop offset="1" stop-color="var(--photo-deep)"/>
        </radialGradient>
      </defs>
      <path fill="url(#heartFill)" d="M345 110 C300 50 250 0 175 0 C70 0 0 85 0 185 C0 320 110 420 345 634 C580 420 691 320 691 185 C691 85 620 0 515 0 C440 0 390 50 345 110 Z"/>
    </svg>
  </main>
</body>
</html>
```